Stationery for use with Ninefold Ridge reports

I would like to get a stationery design that my firm -- Ninefold Ridge Advisory -- will use as a format for reports that we send our clients. I am specifically looking for a design for use on a piece of paper or letterhead -- not business cards or envelopes.

We are an Africa based US risk intelligence and strategy firm that works with multinational corporations operating in West Africa. Our initial thinking is that we would like a color scheme consistent with our existing logo -- however we are open to other color schemes.

Also, we would like to see at least two separate versions: one with our company name and logo, the other without name and logo.

We also would like font recommendations for the stationary design.

The final design should communicate discreet professionalism and a modern approach, but it should not overshadow the words and information printed on the stationery.

Target Market(s)

Multinational corporations that currently use our products.

Font styles to use
Serif
Sans Serif

Requirements
Must have
• Sense of discreet professionalism that will not overshadow the content we put onto the stationery format.
• We would like to see designs with and without our company name/logo.
• Please suggest fonts that would work with the stationery.
Nice to have
• Ideally colors consistent with out existing logo, though we are open to and even encourage other ideas.
Should not have
• No need for business cards or envelopes.

```html
<!DOCTYPE html>
<html lang="en">
<head>
<meta charset="utf-8">
<title>Ninefold Ridge Advisory – Letterhead (unbranded version)</title>
<link rel="stylesheet" href="https://fonts.googleapis.com/css2?family=Open+Sans:wght@400&display=swap">
<style>
  :root {
    --backdrop: #e4e4e4;
    --paper: #ffffff;
    --rule: #1f2d3a;
    --body-text: #676767;
    --band-amber: #e0a84a;
    --band-sky: #a9d4ef;
    --signature-tone: #d9d9d9;
  }
  html, body {
    margin: 0;
    padding: 0;
    width: 1200px;
    height: 960px;
    overflow: hidden;
    background: var(--backdrop);
  }
  .letterhead {
    position: absolute;
    left: 285px;
    top: 30px;
    width: 630px;
    height: 900px;
    background: var(--paper);
    font-family: "Open Sans", sans-serif;
    color: var(--body-text);
  }
  .header-rule {
    position: absolute;
    left: 33px;
    top: 116px;
    width: 564px;
    height: 2px;
    background: var(--rule);
  }
  .letter-date {
    position: absolute;
    left: 62px;
    top: 264px;
    margin: 0;
    font-size: 11.2px;
    line-height: 16px;
  }
  .letter-body {
    position: absolute;
    left: 63px;
    top: 319px;
    width: 520px;
  }
  .letter-body p {
    margin: 0 0 3px;
    font-size: 11.2px;
    line-height: 23px;
  }
  .letter-body .line {
    display: block;
    white-space: nowrap;
  }
  .letter-body .closing-paragraph {
    margin-top: 8px;
  }
  .signature {
    position: absolute;
    left: 440px;
    top: 624px;
    width: 128px;
    height: 40px;
    background: linear-gradient(90deg, var(--paper), var(--signature-tone) 50%, var(--paper));
    border-radius: 20px;
  }
  .signatory {
    position: absolute;
    left: 443px;
    top: 666px;
    margin: 0;
    font-size: 11px;
    line-height: 12.5px;
  }
  .signatory span { display: block; }
  .footer-band {
    position: absolute;
    left: 0;
    bottom: 0;
    width: 630px;
    height: 18px;
    display: block;
  }
</style>
</head>
<body>
  <main class="letterhead">
    <div class="header-rule"></div>

    <p class="letter-date">Date, 10 September, 2020</p>

    <section class="letter-body">
      <p>
        <span class="line">This is a sample letter that has been placed to demonstrate typing remat (Your Company). letterhead</span>
        <span class="line">design. When positioned properly, it will serve to work in harmony with all other elements letterhead.</span>
        <span class="line">This letterhead design is meant to project an image</span>
      </p>
      <p>
        <span class="line">This letterhead design is meant project an image of professionalism reliability. By using simple aligen</span>
        <span class="line">we have created a very spacious feeling. The simplicity suggest&nbsp; rengththe spaciousnes contributes h</span>
        <span class="line">aesthetics the layout. These basic qualities along with the (Your Company)</span>
      </p>
      <p>
        <span class="line">look and helps reinforce the (Your Company) brand. letterhead design is meant to project an image p</span>
        <span class="line">design. When positioned properly, it will serve to work in harmony all the other elements letterhead.</span>
        <span class="line">sionalism and reliability.</span>
      </p>
      <p class="closing-paragraph">
        <span class="line">This letterhead design is based on the (Form of your logo) form (Your Company) logo. Each stationery</span>
        <span class="line">we have created a very spacious feeling. The simplicity suggests strength the spaciousnes contribute</span>
        <span class="line">part of the (Form of your logo).</span>
      </p>
    </section>

    <div class="signature" role="img" aria-label="Handwritten signature of Marcus Adeyemi"></div>
    <p class="signatory">
      <span>Marcus Adeyemi</span>
      <span>Manager</span>
    </p>

    <svg class="footer-band" viewBox="0 0 630 18" aria-hidden="true">
      <polygon points="0,0 517,0 508,18 0,18" fill="var(--band-amber)"/>
      <polygon points="525,0 630,0 630,18 516,18" fill="var(--band-sky)"/>
    </svg>
  </main>
</body>
</html>
```